Graphic Design for a 3 Banner Tradeshow Setup

We are a Pipe Restoration company that specializes in trenchless pipelining. We need a design for a 3 banner setup to use at tradeshows. See attached "banner specs" for sizing - note the 48" x 92" will be in between the two 36" x 92" banners. See attached "Mock-Up" of information each banner needs and utilize the color scheme of the banners we already have in the "both DWM banners" AI file attached. The final designs should communicate what we do and attract people into our booth. We would like to have graphics of realistic pipes for a before (dirty pipe), after cleaning pipe, and lined pipe - see example of "pipe pictures" attached. I'm not sure if this is something you can generate or if we will need to find images of our own to send. Also, see attached "screenshot-process" to see similar images we would like to use to showcase the process.
Target Market(s)
Homeowners, Property Managers, HOA Communities, Healthcare Facilities & Hospitals, and commercial properties
Industry/Entity Type
Trenchless Pipelining
Look and feel

```html
<!DOCTYPE html>
<html lang="en">
<head>
<meta charset="utf-8">
<title>DWM Tradeshow Banners</title>
<link rel="stylesheet" href="https://fonts.googleapis.com/css2?family=Oswald:wght@300;500;700&family=Poppins:wght@600;700&display=swap">
<style>
  :root{
    --stage:#eeeeee;
    --charcoal:#2a2a2a;
    --charcoal-soft:#3a3a3a;
    --white:#ffffff;
    --navy:#24326c;
    --royal:#1f5ca3;
    --accent:#1b8ccc;
    --sky:#2ba3de;
  }
  *{box-sizing:border-box;margin:0;padding:0}
  html,body{width:1200px;height:1161px;overflow:hidden;background:var(--stage)}
  body{position:relative;font-family:"Poppins",sans-serif}

  .banner{position:absolute;width:314px;height:802px;overflow:hidden;
    background:linear-gradient(180deg,var(--charcoal) 0%,var(--charcoal-soft) 60%,var(--charcoal) 100%);
    box-shadow:4px 6px 12px rgba(0,0,0,.28)}
  .banner--assess{left:87px;top:182px}
  .banner--fix{left:444px;top:178px}
  .banner--problems{left:800px;top:178px}

  .brand{position:absolute;top:40px;left:0;right:0;text-align:center;color:var(--white)}
  .brand__name{display:inline-flex;align-items:center;gap:8px;font-family:"Oswald",sans-serif;font-weight:700;font-size:48px;line-height:1;letter-spacing:6px}
  .brand__mark{width:32px;height:32px;background:var(--accent)}
  .brand__tagline{margin-top:4px;font-family:"Oswald",sans-serif;font-weight:300;font-size:10.5px;letter-spacing:2.4px}

  .headline{position:absolute;left:0;right:0;text-align:center;font-family:"Oswald",sans-serif;line-height:1;text-transform:uppercase}
  .headline--thin{font-weight:300;color:var(--accent)}
  .headline--bold{font-weight:700;color:var(--white)}
  .headline .blue{color:var(--accent)}

  .card{position:absolute;left:0;right:0;bottom:0;background:var(--white);border-radius:22px 22px 0 0}
  .panel{position:absolute;left:17px;right:17px;top:9px;bottom:0;border-radius:14px 14px 0 0;
    background:linear-gradient(180deg,var(--royal) 0%,#21479a 45%,var(--navy) 100%);color:var(--white)}

  .service{position:absolute;text-align:center;font-weight:600;font-size:12.5px;line-height:1.2;white-space:nowrap}
  .service--wide{width:110px}
  .service--narrow{width:96px;font-size:12px}
  .service__icon{display:block;margin:0 auto 8px;width:52px;height:52px}
  .grid-line{position:absolute;border:0 dashed rgba(255,255,255,.55)}
  .grid-line--v{border-left-width:1px}
  .grid-line--h{border-top-width:1px}

  .cta{position:absolute;left:21px;right:21px;height:28px;border-radius:3px;background:var(--white);padding:2px}
  .cta__inner{height:100%;background:var(--sky);text-align:center;font-weight:700;font-size:19px;line-height:24px;color:var(--white);letter-spacing:.3px}
  .phone{position:absolute;left:0;right:0;display:flex;justify-content:center;align-items:center;gap:8px;
    font-family:"Oswald",sans-serif;font-weight:500;font-size:34px;line-height:1;color:var(--white)}
  .web{position:absolute;left:0;right:0;text-align:center;font-weight:600;font-size:12.5px;color:var(--white)}
  .web .blue{color:var(--sky)}

  .photo{position:absolute;border:1px solid rgba(255,255,255,.6);border-radius:6px;
    background:linear-gradient(160deg,#8a8f96 0%,#3f5c86 55%,#23344f 100%)}
  .pipes{position:absolute;left:32px;width:260px;top:350px;height:66px;border-radius:8px;z-index:2;
    background:linear-gradient(180deg,#5a524c 0%,#3c3a3a 100%)}

  .pitch{position:absolute;left:0;right:0;text-align:center;font-weight:700;line-height:1.2}
</style>
</head>
<body>

<section class="banner banner--assess">
  <div class="brand"><div class="brand__name"><span class="brand__mark"></span>DWM</div><div class="brand__tagline">DRAIN WORKS MANAGEMENT</div></div>
  <div class="headline headline--thin" style="top:134px;font-size:70px">We</div>
  <div class="headline headline--bold" style="top:206px;font-size:74px;letter-spacing:-1px">Assess</div>
  <div class="card" style="top:312px">
    <div class="panel">
      <span class="grid-line grid-line--v" style="left:140px;top:62px;height:120px"></span>
      <span class="grid-line grid-line--v" style="left:140px;top:205px;height:110px"></span>
      <span class="grid-line grid-line--h" style="left:24px;width:105px;top:192px"></span>
      <span class="grid-line grid-line--h" style="left:152px;width:105px;top:192px"></span>
      <div class="service service--wide" style="left:15px;top:53px">
        <svg class="service__icon" viewBox="0 0 52 52"><circle cx="26" cy="26" r="24" fill="#1b8ccc" stroke="#fff" stroke-width="1.5"/><rect x="15" y="20" width="18" height="11" rx="2" fill="#fff"/><path d="M33 23l6-3v11l-6-3z" fill="#fff"/></svg>CCTV Pipe<br>Investigation</div>
      <div class="service service--wide" style="left:155px;top:53px">
        <svg class="service__icon" viewBox="0 0 52 52"><circle cx="26" cy="26" r="24" fill="#1b8ccc" stroke="#fff" stroke-width="1.5"/><path d="M26 14a12 12 0 1 0 12 12H26z" fill="#fff"/><path d="M28 12v12h12a12 12 0 0 0-12-12z" fill="#fff"/></svg>Budgetary<br>Evaluation</div>
      <div class="service service--wide" style="left:15px;top:212px">
        <svg class="service__icon" viewBox="0 0 52 52"><circle cx="26" cy="26" r="24" fill="#1b8ccc" stroke="#fff" stroke-width="1.5"/><rect x="17" y="13" width="16" height="22" rx="1.5" fill="#fff"/><path d="M20 19h10M20 24h10M20 29h6" stroke="#1b8ccc" stroke-width="2"/></svg>Scope<br>Development</div>
      <div class="service service--wide" style="left:155px;top:216px">
        <svg class="service__icon" viewBox="0 0 52 52"><circle cx="26" cy="26" r="24" fill="#1b8ccc" stroke="#fff" stroke-width="1.5"/><circle cx="26" cy="24" r="8" fill="none" stroke="#fff" stroke-width="3"/><path d="M26 12v4M26 32v4M14 24h4M34 24h4M22 38h8" stroke="#fff" stroke-width="3"/></svg>Project<br>Oversight</div>
      <div class="cta" style="top:329px"><div class="cta__inner">CONTACT US NOW!</div></div>
      <div class="phone" style="top:373px"><svg width="30" height="30" viewBox="0 0 30 30"><circle cx="15" cy="15" r="15" fill="#2ba3de"/><path d="M10 8l3 0 1.5 4-2 1.5a9 9 0 0 0 4 4l1.5-2 4 1.5v3a2 2 0 0 1-2 2A13 13 0 0 1 8 10a2 2 0 0 1 2-2z" fill="#fff"/></svg>1-800-555-0142</div>
      <div class="web" style="top:420px">www.<span class="blue">drainworksmanagement</span>.com</div>
    </div>
  </div>
</section>

<section class="banner banner--fix">
  <div class="brand"><div class="brand__name"><span class="brand__mark"></span>DWM</div><div class="brand__tagline">DRAIN WORKS MANAGEMENT</div></div>
  <div class="headline headline--bold" style="top:126px;font-size:78px;letter-spacing:-1px">We <span class="blue">Fix</span></div>
  <div class="photo" style="left:28px;top:229px;width:126px;height:116px" role="img" aria-label="Technician inspecting a pipe camera monitor"></div>
  <div class="photo" style="left:160px;top:229px;width:126px;height:116px" role="img" aria-label="Crew working on an open pipe access point"></div>
  <div class="card" style="top:364px">
    <div class="panel">
      <span class="grid-line grid-line--v" style="left:94px;top:25px;height:110px"></span>
      <span class="grid-line grid-line--v" style="left:193px;top:25px;height:110px"></span>
      <span class="grid-line grid-line--v" style="left:94px;top:150px;height:100px"></span>
      <span class="grid-line grid-line--v" style="left:193px;top:150px;height:100px"></span>
      <span class="grid-line grid-line--h" style="left:16px;width:70px;top:133px"></span>
      <span class="grid-line grid-line--h" style="left:103px;width:82px;top:133px"></span>
      <span class="grid-line grid-line--h" style="left:203px;width:62px;top:133px"></span>
      <div class="service service--narrow" style="left:-1px;top:24px">
        <svg class="service__icon" viewBox="0 0 52 52"><circle cx="26" cy="26" r="24" fill="#1b8ccc" stroke="#fff" stroke-width="1.5"/><path d="M18 14v24M34 14v24M18 26h16" stroke="#fff" stroke-width="4"/></svg>Slow<br>Drains</div>
      <div class="service service--narrow" style="left:95px;top:24px">
        <svg class="service__icon" viewBox="0 0 52 52"><circle cx="26" cy="26" r="24" fill="#1b8ccc" stroke="#fff" stroke-width="1.5"/><rect x="20" y="13" width="8" height="14" fill="#fff"/><path d="M14 31q3-3 6 0t6 0 6 0 6 0M14 37q3-3 6 0t6 0 6 0 6 0" stroke="#fff" stroke-width="2.5" fill="none"/></svg>Back-Ups</div>
      <div class="service service--narrow" style="left:188px;top:24px">
        <svg class="service__icon" viewBox="0 0 52 52"><circle cx="26" cy="26" r="24" fill="#1b8ccc" stroke="#fff" stroke-width="1.5"/><path d="M16 14h20M16 19h20M22 24v12h8V24M14 38h24" stroke="#fff" stroke-width="2.5" fill="none"/></svg>Sewer<br>Odors</div>
      <div class="service service--narrow" style="left:-1px;top:152px">
        <svg class="service__icon" viewBox="0 0 52 52"><circle cx="26" cy="26" r="24" fill="#1b8ccc" stroke="#fff" stroke-width="1.5"/><rect x="13" y="22" width="26" height="10" rx="2" fill="#fff"/><path d="M24 22l3 5-3 5" stroke="#1b8ccc" stroke-width="2" fill="none"/></svg>Cracked<br>Pipes</div>
      <div class="service service--narrow" style="left:95px;top:152px">
        <svg class="service__icon" viewBox="0 0 52 52"><circle cx="26" cy="26" r="24" fill="#1b8ccc" stroke="#fff" stroke-width="1.5"/><path d="M16 16h16v8" stroke="#fff" stroke-width="4" fill="none"/><circle cx="30" cy="32" r="5" fill="none" stroke="#fff" stroke-width="2.5"/><path d="M34 36l4 4" stroke="#fff" stroke-width="3"/></svg>Recurring<br>Plumbing<br>Problems</div>
      <div class="service service--narrow" style="left:188px;top:152px">
        <svg class="service__icon" viewBox="0 0 52 52"><circle cx="26" cy="26" r="24" fill="#1b8ccc" stroke="#fff" stroke-width="1.5"/><circle cx="28" cy="23" r="8" fill="none" stroke="#fff" stroke-width="3"/><path d="M22 29l-7 8" stroke="#fff" stroke-width="4"/></svg>Root<br>Intrusion</div>
      <div class="cta" style="top:277px"><div class="cta__inner">CONTACT US NOW!</div></div>
      <div class="phone" style="top:321px"><svg width="30" height="30" viewBox="0 0 30 30"><circle cx="15" cy="15" r="15" fill="#2ba3de"/><path d="M10 8l3 0 1.5 4-2 1.5a9 9 0 0 0 4 4l1.5-2 4 1.5v3a2 2 0 0 1-2 2A13 13 0 0 1 8 10a2 2 0 0 1 2-2z" fill="#fff"/></svg>1-800-555-0142</div>
      <div class="web" style="top:368px">www.<span class="blue">drainworksmanagement</span>.com</div>
    </div>
  </div>
</section>

<section class="banner banner--problems">
  <div class="brand"><div class="brand__name"><span class="brand__mark"></span>DWM</div><div class="brand__tagline">DRAIN WORKS MANAGEMENT</div></div>
  <div class="headline headline--thin" style="top:140px;font-size:86px">Pipe</div>
  <div class="headline headline--bold" style="top:226px;font-size:56px">Problems?</div>
  <div class="pipes" role="img" aria-label="Photo of cut pipe sections showing a corroded pipe, a cleaned pipe and a newly lined pipe"></div>
  <div class="card" style="top:376px">
    <div class="panel">
      <div class="pitch" style="top:70px;font-size:20px">We help fix pipe<br>problems without<br>having to</div>
      <div class="pitch" style="top:160px;font-size:27px;color:var(--sky)">TEAR UP</div>
      <div class="pitch" style="top:191px;font-size:27px">YOUR BUILDING</div>
      <div class="cta" style="top:267px"><div class="cta__inner">CONTACT US NOW!</div></div>
      <div class="phone" style="top:311px"><svg width="30" height="30" viewBox="0 0 30 30"><circle cx="15" cy="15" r="15" fill="#2ba3de"/><path d="M10 8l3 0 1.5 4-2 1.5a9 9 0 0 0 4 4l1.5-2 4 1.5v3a2 2 0 0 1-2 2A13 13 0 0 1 8 10a2 2 0 0 1 2-2z" fill="#fff"/></svg>1-800-555-0142</div>
      <div class="web" style="top:358px">www.<span class="blue">drainworksmanagement</span>.com</div>
    </div>
  </div>
</section>

</body>
</html>
```